Brellwick Partners, LLC Stationary

Brellwick Partners, LLC is a new financial planning and consulting company. We are looking for designs on business cards, letterhead, envelopes, and anything else that would be useful. Our preference for business card design is two sided. We are looking for a professional and clean look with incorporating the logo and patriotic feel. Thank you to all who participate and good luck!

```html
<!DOCTYPE html>
<html lang="en">
<head>
<meta charset="utf-8">
<title>Brellwick Partners, LLC — Business Card</title>
<link rel="stylesheet" href="https://fonts.googleapis.com/css2?family=Arimo:wght@400;700&display=swap">
<style>
  :root {
    --navy: #1f3a6b;
    --red: #c4202b;
    --red-dark: #8f1720;
    --ink: #3c3c3c;
    --rule: #b9b9b9;
    --paper: #ffffff;
    --backdrop: #e9e6e1;
  }
  * { box-sizing: border-box; margin: 0; padding: 0; }
  html, body { width: 1200px; height: 950px; overflow: hidden; }
  body {
    background: var(--backdrop);
    font-family: "Arimo", Arial, sans-serif;
    position: relative;
  }
  .card {
    position: absolute;
    left: 250px;
    width: 700px;
    height: 400px;
    box-shadow: 0 6px 18px rgba(0,0,0,0.18);
    overflow: hidden;
  }
  /* Front */
  .card-front { top: 40px; background: var(--paper); }
  .brand {
    position: absolute;
    top: 92px;
    left: 0;
    right: 0;
    text-align: center;
  }
  .brand-name {
    display: inline-flex;
    align-items: center;
    gap: 14px;
    font-size: 38px;
    font-weight: 700;
    color: var(--navy);
    letter-spacing: 0.5px;
  }
  .brand-mark {
    width: 22px; height: 22px;
    background: var(--red);
  }
  .brand-tagline {
    margin-top: 8px;
    font-size: 12px;
    letter-spacing: 2.2px;
    color: var(--red);
    text-transform: uppercase;
  }
  .details {
    position: absolute;
    top: 200px;
    left: 0; right: 0;
    display: flex;
    justify-content: center;
  }
  .person {
    text-align: right;
    padding-right: 26px;
    border-right: 1px solid var(--rule);
    color: var(--ink);
    font-size: 17px;
    line-height: 1.45;
  }
  .person-name { font-size: 21px; font-weight: 700; color: var(--navy); }
  .person-title { color: var(--red); font-size: 17px; margin-bottom: 4px; }
  .contacts {
    list-style: none;
    padding-left: 26px;
    padding-top: 24px;
    color: var(--ink);
    font-size: 17px;
    line-height: 1.55;
  }
  .contacts li { display: flex; align-items: center; gap: 10px; }
  .contacts svg { width: 16px; height: 16px; fill: var(--navy); flex: none; }
  .band {
    position: absolute;
    left: 0; right: 0; bottom: 0;
    height: 58px;
    background: var(--navy);
    border-top: 3px solid var(--red);
    box-shadow: 0 -4px 0 var(--paper), 0 -5px 0 var(--red);
  }
  /* Back */
  .card-back {
    top: 510px;
    background: linear-gradient(135deg, var(--red) 0%, var(--red-dark) 100%);
    color: var(--paper);
    display: flex;
    flex-direction: column;
    align-items: center;
    justify-content: center;
  }
  .back-name {
    display: inline-flex;
    align-items: center;
    gap: 14px;
    font-size: 40px;
    font-weight: 700;
    color: var(--paper);
  }
  .back-mark { width: 22px; height: 22px; background: var(--paper); }
  .back-web {
    margin-top: 22px;
    font-size: 18px;
    letter-spacing: 1.5px;
    color: var(--paper);
  }
</style>
</head>
<body>

  <section class="card card-front">
    <div class="brand">
      <div class="brand-name"><span class="brand-mark"></span>Brellwick Partners, LLC</div>
      <div class="brand-tagline">Financial Planning and Consulting</div>
    </div>

    <div class="details">
      <div class="person">
        <div class="person-name">Marcus Hale</div>
        <div class="person-title">President</div>
        <div>2170 Linden Court</div>
        <div>Harbor Vale, NY 11920</div>
      </div>
      <ul class="contacts">
        <li>
          <svg viewBox="0 0 16 16" aria-hidden="true"><path d="M3 1h3l1.5 4-2 1.3a9 9 0 0 0 4.2 4.2L11 8.5l4 1.5v3a2 2 0 0 1-2 2A12 12 0 0 1 1 3a2 2 0 0 1 2-2z"/></svg>
          555 0142 7788
        </li>
        <li>
          <svg viewBox="0 0 16 16" aria-hidden="true"><path d="M4 1h7v4H4zM1 6h14v7h-3v2H4v-2H1zM5 10v4h6v-4z"/></svg>
          555 0193 4410
        </li>
        <li>
          <svg viewBox="0 0 16 16" aria-hidden="true"><path d="M1 3h14v10H1zM2 4.5v.6l6 4 6-4v-.6z"/></svg>
          marcus@brellwick.com
        </li>
        <li>
          <svg viewBox="0 0 16 16" aria-hidden="true"><path d="M8 1a7 7 0 1 0 0 14A7 7 0 0 0 8 1zm0 1.5c.8 0 1.8 1.8 2 4.5H6c.2-2.7 1.2-4.5 2-4.5zM2.6 7H4.5a12 12 0 0 1 .8-3.9A5.5 5.5 0 0 0 2.6 7zm0 2a5.5 5.5 0 0 0 2.7 3.9A12 12 0 0 1 4.5 9zM6 9h4c-.2 2.7-1.2 4.5-2 4.5S6.2 11.7 6 9zm5.5 0h1.9a5.5 5.5 0 0 1-2.7 3.9c.4-1 .7-2.4.8-3.9zm1.9-2h-1.9a12 12 0 0 0-.8-3.9A5.5 5.5 0 0 1 13.4 7z"/></svg>
          www.brellwick.com
        </li>
      </ul>
    </div>

    <div class="band"></div>
  </section>

  <section class="card card-back">
    <div class="back-name"><span class="back-mark"></span>Brellwick Partners, LLC</div>
    <div class="back-web">www.brellwick.com</div>
  </section>

</body>
</html>
```